Card Design for my dog training business Brightpaw Obedience

Need a business card design for my dog training business with my new logo. Want the card to come off professional yet fun. Want it to be very eye catchy as well. I normally have these at vet clinics, pet stores, and groomers. so need it to look better than my competitors.
Target Market(s)
dog owners
Industry/Entity Type
Dog Training
Contact Information for Business Card
needs logo, my name and info
Font styles to use
Serif
Colors
0255a3
ffffff
ec1f27
000000
333333
fbfbfb
Requirements
Must have
- Brightpaw Obedience
- Felix Orland
- 415 903 2276
- info@brightpawobedience.example
- www.brightpawobedience.example

```html
<!DOCTYPE html>
<html lang="en">
<head>
<meta charset="UTF-8">
<title>Brightpaw Obedience — Business Card</title>
<link href="https://fonts.googleapis.com/css2?family=EB+Garamond:ital,wght@0,400;0,600;1,400&display=swap" rel="stylesheet">
<style>
  :root {
    --stage: #2b2b2e;
    --card-white: #ffffff;
    --card-black: #000000;
    --ink: #111111;
    --ink-soft: #333333;
    --on-dark: #fbfbfb;
    --art-light: #ececec;
    --art-dark: #bdbdbd;
    --serif: "EB Garamond", "Times New Roman", serif;
  }
  * { margin: 0; padding: 0; box-sizing: border-box; }
  html, body { width: 1200px; height: 800px; overflow: hidden; }
  body {
    background: var(--stage);
    font-family: var(--serif);
    position: relative;
  }
  .card {
    position: absolute;
    top: 245px;
    width: 525px;
    height: 300px;
    border-radius: 22px;
    overflow: hidden;
    box-shadow: 0 16px 40px rgba(0,0,0,.45);
  }
  .card--front { left: 50px; background: var(--card-white); }
  .card--back { left: 625px; display: flex; }

  .brand {
    display: flex;
    flex-direction: column;
    align-items: center;
    justify-content: center;
    text-align: center;
    color: var(--ink);
    height: 100%;
  }
  .brand__art {
    width: 230px;
    height: 120px;
    border-radius: 10px;
    background: radial-gradient(ellipse at 55% 45%, var(--art-dark) 0%, var(--art-light) 75%);
  }
  .brand__name {
    font-size: 28px;
    font-weight: 600;
    letter-spacing: 1px;
    line-height: 1;
    white-space: nowrap;
    margin-top: 14px;
  }
  .brand__rule {
    width: 230px;
    height: 1px;
    background: var(--ink);
    margin: 10px 0 10px;
  }
  .brand__tagline {
    font-style: italic;
    font-size: 12px;
    color: var(--ink-soft);
    white-space: nowrap;
  }

  .back__logo-panel {
    width: 44%;
    background: var(--card-white);
  }
  .back__logo-panel .brand__art { width: 175px; height: 95px; }
  .back__logo-panel .brand__name { font-size: 20px; margin-top: 12px; }
  .back__logo-panel .brand__rule { width: 185px; margin: 8px 0; }
  .back__logo-panel .brand__tagline { font-size: 9.5px; }

  .back__info {
    flex: 1;
    background: var(--card-black);
    color: var(--on-dark);
    padding: 44px 20px 0 30px;
  }
  .person__name {
    font-size: 21px;
    font-weight: 600;
    letter-spacing: 1px;
    text-transform: uppercase;
  }
  .person__role { font-size: 16px; margin-bottom: 18px; }
  .company { font-size: 15px; line-height: 1.3; margin-bottom: 14px; }
  .contact { list-style: none; font-size: 13px; line-height: 1.55; }
  .contact li { display: flex; align-items: center; gap: 8px; white-space: nowrap; }
  .contact svg { width: 12px; height: 12px; flex: none; fill: var(--on-dark); }
  .social {
    display: flex;
    gap: 5px;
    justify-content: flex-end;
    margin-top: 14px;
  }
  .social span {
    width: 18px; height: 18px;
    background: var(--on-dark);
    border-radius: 2px;
  }
</style>
</head>
<body>

  <section class="card card--front" aria-label="Business card front">
    <div class="brand">
      <div class="brand__art" role="img" aria-label="Logo illustration: two dog heads inside a Texas state outline"></div>
      <p class="brand__name">Brightpaw Obedience</p>
      <div class="brand__rule"></div>
      <p class="brand__tagline">“Training dogs across Texas one dog at a time.”</p>
    </div>
  </section>

  <section class="card card--back" aria-label="Business card back">
    <div class="back__logo-panel">
      <div class="brand">
        <div class="brand__art" role="img" aria-label="Logo illustration: two dog heads inside a Texas state outline"></div>
        <p class="brand__name">Brightpaw Obedience</p>
        <div class="brand__rule"></div>
        <p class="brand__tagline">“Training dogs across Texas one dog at a time.”</p>
      </div>
    </div>

    <div class="back__info">
      <h1 class="person__name">Felix Orland</h1>
      <p class="person__role">Trainer</p>
      <p class="company">Brightpaw Obedience<br>Cedar Hollow, Tx</p>
      <ul class="contact">
        <li>
          <svg viewBox="0 0 24 24" aria-hidden="true"><path d="M6.6 10.8a15 15 0 0 0 6.6 6.6l2.2-2.2a1 1 0 0 1 1-.25 11.4 11.4 0 0 0 3.6.57 1 1 0 0 1 1 1V20a1 1 0 0 1-1 1A17 17 0 0 1 3 4a1 1 0 0 1 1-1h3.5a1 1 0 0 1 1 1c0 1.25.2 2.450.57 3.6a1 1 0 0 1-.25 1z"/></svg>
          415 903 2276
        </li>
        <li>
          <svg viewBox="0 0 24 24" aria-hidden="true"><path d="M2 5h20v14H2z M3.5 6.5 12 13l8.5-6.5" fill="none" stroke="#fbfbfb" stroke-width="2"/></svg>
          info@brightpawobedience.example
        </li>
        <li>
          <svg viewBox="0 0 24 24" aria-hidden="true"><circle cx="12" cy="12" r="9" fill="none" stroke="#fbfbfb" stroke-width="2"/><path d="M3 12h18M12 3c3 3.5 3 14.5 0 18M12 3c-3 3.5-3 14.5 0 18" fill="none" stroke="#fbfbfb" stroke-width="1.5"/></svg>
          www.brightpawobedience.example
        </li>
      </ul>
      <div class="social" aria-hidden="true"><span></span><span></span></div>
    </div>
  </section>

</body>
</html>
```